Falkrin homes and renovations business card design.

Would like some new card designs utilizing my new logo that look professional. I am open to different colors on the logo or utilize the same ones we have. I like the original concept but would like to see some fresh ideas and build on what we have already done.

Target Market(s)

Custom home building industry, Real estate sales, Renovation projects.

Industry/Entity Type

Home Builder

Contact Information for Business Card

Falkrin Homes and Renovations
2871 96th Avenue
Corvell, Alberta
T2R3W8
Home : 403- 718-4063 Cell: 403- 294-5170

My info is : Dax Falkrin, President and CEO
email: falkrinhomes@maildrop-example.net
Website: falkrinhomes-example.com
websit

Requirements
Must have
• Must Use my new logo design. I am open to different colors on the logo or utilize the same ones in the existing design. I can upload the original logo design if needed.

```html
<!DOCTYPE html>
<html lang="en">
<head>
<meta charset="utf-8">
<title>Falkrin Homes and Renovations – Business Card</title>
<link rel="stylesheet" href="https://fonts.googleapis.com/css2?family=Oswald:wght@500&family=Open+Sans:wght@400;600&display=swap">
<style>
  :root {
    --page: #202020;
    --card: #262626;
    --card-edge: #303030;
    --ink-white: #f2f2f2;
    --ink-grey: #cfcfcf;
    --ink-muted: #9a9a9a;
    --accent: #f0b323;
    --logo-silver: #b9b9b9;
    --divider: #6a6a6a;
  }
  * { box-sizing: border-box; margin: 0; padding: 0; }
  html, body {
    width: 1200px; height: 1000px; overflow: hidden;
    background: var(--page);
    font-family: "Open Sans", Arial, sans-serif;
  }
  .canvas {
    position: relative; width: 1200px; height: 1000px;
    display: flex; flex-direction: column; align-items: center; justify-content: center; gap: 48px;
  }
  .card {
    position: relative; width: 700px; height: 400px;
    background: var(--card);
    border: 1px solid var(--card-edge);
    box-shadow: 0 18px 40px rgba(0,0,0,.45);
  }

  /* Back side */
  .card-back .brand {
    position: absolute; left: 0; right: 0; top: 140px;
    display: flex; flex-direction: column; align-items: center; gap: 10px;
    color: var(--logo-silver);
  }
  .brand-row { display: flex; align-items: center; gap: 14px; }
  .brand-mark { width: 22px; height: 22px; background: var(--logo-silver); }
  .brand-name {
    font-weight: 600; font-size: 44px; letter-spacing: 3px; line-height: 1;
    text-transform: uppercase;
  }
  .brand-tagline {
    font-weight: 600; font-size: 15px; letter-spacing: 2px; text-transform: uppercase;
  }
  .card-back .web {
    position: absolute; left: 0; right: 0; bottom: 38px;
    display: flex; justify-content: center; align-items: center; gap: 10px;
    color: var(--ink-grey); font-size: 17px; letter-spacing: .5px;
  }
  .accent { color: var(--accent); }

  /* Front side */
  .identity {
    position: absolute; left: 40px; top: 130px; width: 240px; text-align: right;
  }
  .person-name {
    font-family: "Oswald", "Arial Narrow", sans-serif; font-weight: 500;
    font-size: 42px; letter-spacing: 2px; line-height: 1.05; color: var(--ink-white);
    text-transform: uppercase;
  }
  .person-role { color: var(--accent); font-weight: 600; font-size: 17px; margin-top: 2px; }
  .divider {
    position: absolute; left: 300px; top: 128px; width: 2px; height: 88px; background: var(--divider);
  }
  .contacts {
    position: absolute; left: 320px; top: 126px; list-style: none;
    color: var(--ink-grey); font-size: 17px; line-height: 23px; letter-spacing: .4px;
  }
  .contacts li { display: flex; align-items: center; gap: 14px; white-space: nowrap; }
  .contacts svg { width: 16px; height: 16px; flex: none; }
  .footer {
    position: absolute; left: 40px; bottom: 48px;
    display: flex; align-items: center; gap: 14px;
    color: var(--ink-grey); font-size: 17px; letter-spacing: .6px;
  }
  .mini-brand { display: flex; align-items: center; gap: 6px; color: var(--accent); font-weight: 600; font-size: 11px; letter-spacing: .5px; text-transform: uppercase; }
  .mini-mark { width: 9px; height: 9px; background: var(--accent); }
</style>
</head>
<body>
<main class="canvas">

  <section class="card card-back" aria-label="Card back">
    <div class="brand">
      <div class="brand-row">
        <span class="brand-mark"></span>
        <span class="brand-name">Falkrin</span>
      </div>
      <span class="brand-tagline">Falkrin Homes and Renovations</span>
    </div>
    <p class="web">
      <svg width="16" height="16" viewBox="0 0 16 16" aria-hidden="true"><circle cx="8" cy="8" r="7" fill="var(--accent)"/><path d="M1 8h14M8 1c3 3 3 11 0 14M8 1c-3 3-3 11 0 14" stroke="var(--card)" stroke-width="1" fill="none"/></svg>
      <span>www.<span class="accent">falkrinhomes-example</span>.com</span>
    </p>
  </section>

  <section class="card card-front" aria-label="Card front">
    <div class="identity">
      <h1 class="person-name">Dax Falkrin</h1>
      <p class="person-role">President and CEO</p>
    </div>
    <span class="divider"></span>
    <ul class="contacts">
      <li>
        <svg viewBox="0 0 16 16" aria-hidden="true"><path d="M3 1h3l1.5 4-2 1.2a9 9 0 0 0 4.3 4.3L11 8.5l4 1.5v3a2 2 0 0 1-2 2A12 12 0 0 1 1 3a2 2 0 0 1 2-2z" fill="var(--accent)"/></svg>
        <span>403 718 4063</span>
      </li>
      <li>
        <svg viewBox="0 0 16 16" aria-hidden="true"><rect x="4" y="1" width="8" height="14" rx="1.5" fill="none" stroke="var(--accent)" stroke-width="1.6"/><circle cx="8" cy="12.5" r=".9" fill="var(--accent)"/></svg>
        <span>403 294 5170</span>
      </li>
      <li>
        <svg viewBox="0 0 16 16" aria-hidden="true"><rect x="1" y="3" width="14" height="10" fill="var(--accent)"/><path d="M1 3l7 5.5L15 3" stroke="var(--card)" stroke-width="1.3" fill="none"/></svg>
        <span>falkrinhomes@maildrop-example.net</span>
      </li>
      <li>
        <svg viewBox="0 0 16 16" aria-hidden="true"><circle cx="9.5" cy="6.5" r="4.5" fill="none" stroke="var(--accent)" stroke-width="1.8"/><path d="M6.3 9.7L1.5 14.5" stroke="var(--accent)" stroke-width="2"/></svg>
        <span>www.<span class="accent">falkrinhomes-example</span>.com</span>
      </li>
    </ul>
    <div class="footer">
      <span class="mini-brand"><span class="mini-mark"></span>Falkrin Homes</span>
      <span>- &nbsp;2871 96th Avenue Corvell, Alberta</span>
    </div>
  </section>

</main>
</body>
</html>
```